Online interactive tutorial for year 2 to year 12 students in Australia

Website design for a new online tutorial for year 2 to year 12 students in Australia.

- The tutorial will be conducted via live webcam and within a dedicated interactive space
- The tutorial will be provided by high scoring undergraduates studying in top Australian universities.
- The tutors will be going through interviews & assessments & only top students are allowed to apply.
- Parents will do search and select tutor and have short 15 mins video interaction with potential tutors before booking them for their children for tutoring.
- hourly cost of booking (no monthly subscription or no hour limits)
- Tutors will have their own profile

Please see the attached for detailed page functionality.

The look and feel of the design must consider the following:
- must be educational but not dull and should stand out
- must appeal to younger generation - tutees (8-18 years), tutors (19-25), parents (30-50).
- Ideas for Logos (brivora.com.au but not confirmed)

Target Market(s)

tutees (8-18 years), tutors (19-25 years), parents (30-50 years).

Industry/Entity Type

Education

Coding

Coded - Design and coding required

Number of Pages Required

5+ page

Font styles to use
Serif

Requirements
Must have
• The look and feel of the design must consider the following:
• - must be educational but not dull and should stand out
• - must appeal to younger generation - tutees (8-18 years), tutors (19-25), parents (30-50).
Should not have
• Dullness

```html
<!DOCTYPE html>
<html lang="en">
<head>
<meta charset="utf-8">
<title>Brivora — Online Tutoring</title>
<link href="https://fonts.googleapis.com/css2?family=Montserrat:wght@400;500;600&family=Open+Sans:wght@400;600&display=swap" rel="stylesheet">
<style>
:root{
  --blue:#2d5bd3;
  --ink:#1d1d1f;
  --text:#6a6f7a;
  --grey-bg:#f2f2f2;
  --dark:#17171a;
  --line:#d8d8d8;
  --white:#ffffff;
}
*{box-sizing:border-box;margin:0;padding:0}
html,body{width:1200px;height:2594px;overflow:hidden;background:var(--white)}
body{position:relative;font-family:"Open Sans",sans-serif;color:var(--text)}
.abs{position:absolute}
.center{text-align:center}

/* header */
.logo{left:233px;top:16px;font-family:"Montserrat",sans-serif;font-size:30px;font-weight:500;color:var(--ink)}
.btn{position:absolute;top:22px;height:27px;width:97px;font-family:"Montserrat",sans-serif;font-size:9px;letter-spacing:1.5px;display:flex;align-items:center;justify-content:center;text-transform:uppercase;border-radius:2px}
.btn-login{left:769px;border:1px solid var(--ink);color:var(--ink)}
.btn-register{left:869px;background:var(--blue);color:var(--white)}
.header-rule{left:233px;top:71px;width:732px;height:1px;background:var(--line)}
.nav{left:248px;top:87px;width:700px;display:flex;justify-content:space-between;font-family:"Montserrat",sans-serif;font-size:10.5px;color:#444}
.nav .active{color:var(--blue)}

/* hero */
.hero{left:0;top:119px;width:1200px;height:453px;background:radial-gradient(ellipse at 55% 40%,#4a4d52 0%,#2c2e33 55%,#1b1c20 100%)}
.hero-sub{top:256px;width:1200px;font-size:10px;color:#e6e6e6}
.hero-title{top:280px;width:1200px;font-family:"Montserrat",sans-serif;font-size:20px;line-height:23px;color:var(--white)}
.hero-btn{position:absolute;top:403px;height:35px;width:125px;font-family:"Montserrat",sans-serif;font-size:9.5px;letter-spacing:1.8px;display:flex;align-items:center;justify-content:center;color:var(--white);text-transform:uppercase}
.hero-more{left:465px;border:1.5px solid var(--white)}
.hero-contact{left:609px;background:var(--blue)}

/* section headings */
.section-title{width:1200px;font-family:"Montserrat",sans-serif;font-size:16px;font-weight:500;color:var(--ink);letter-spacing:.5px}
.divider{left:570px;width:60px;height:12px}
.body-copy{font-size:10px;line-height:15.5px;color:var(--text)}

.who{left:0;top:572px;width:1200px;height:329px;background:var(--grey-bg)}

/* tutors */
.tutor-photo{position:absolute;top:1032px;width:200px;height:216px}
.tutor-card{left:400px;top:1032px;width:200px;height:216px;background:var(--blue);color:var(--white)}
.tutor-name{top:34px;width:200px;font-family:"Montserrat",sans-serif;font-size:9.5px;letter-spacing:2px}
.tutor-bio{top:78px;left:15px;width:170px;font-size:9px;line-height:15.5px}

/* services */
.services{left:0;top:1248px;width:1200px;height:431px;background:linear-gradient(180deg,#e9e8e4 0%,#dcd6cc 50%,#cfc8bd 100%)}
.service-card{position:absolute;top:1390px;width:231px;height:249px;background:var(--white)}
.service-card svg{position:absolute;left:100px;top:35px}
.service-card .rule{position:absolute;left:106px;top:79px;width:19px;height:1.5px;background:var(--blue)}
.service-card h3{position:absolute;top:90px;width:231px;font-family:"Montserrat",sans-serif;font-size:9.5px;font-weight:600;letter-spacing:1.8px;color:var(--ink);text-align:center}
.service-card p{position:absolute;top:130px;left:25px;width:181px;font-size:9px;line-height:15.5px;text-align:center}

/* clients */
.client{position:absolute;top:1968px;width:130px;display:flex;align-items:center;justify-content:center;gap:6px;font-family:"Montserrat",sans-serif;font-size:11px;font-weight:600;color:var(--ink)}
.client i{width:9px;height:9px;border-radius:50%;background:var(--ink);display:block}

/* footer */
.footer{left:0;top:2127px;width:1200px;height:384px;background:var(--dark)}
.footer-box{position:absolute;top:2161px;height:313px;border:1px solid #55565c}
.footer-title{position:absolute;top:52px;width:100%;text-align:center;font-family:"Montserrat",sans-serif;font-size:15px;color:var(--white)}
.field-label{position:absolute;left:43px;font-family:"Montserrat",sans-serif;font-size:9px;color:var(--white);letter-spacing:.5px}
.field-line{position:absolute;left:43px;width:270px;height:1px;background:#5c5d63}
.bottom-bar{left:0;top:2511px;width:1200px;height:83px;background:var(--blue)}
.social{position:absolute;top:2548px;width:10px;height:10px;border-radius:50%;background:var(--white)}
</style>
</head>
<body>

<!-- header -->
<div class="abs logo">Brivora</div>
<div class="btn btn-login">Login</div>
<div class="btn btn-register">Register</div>
<div class="abs header-rule"></div>
<nav class="abs nav">
  <span class="active">Home</span><span>Registrations</span><span>Note Space</span><span>Tutors Profile</span><span>Scheduler</span><span>Feed Back</span><span>About Us</span><span>Contact Us</span><span>Message</span>
</nav>

<!-- hero -->
<div class="abs hero" role="img" aria-label="Desk seen from above with laptop on a video call, notebooks and coffee cups"></div>
<div class="abs hero-sub center">Lorem ipsum dolor sit amet, consectetur adipiscing</div>
<div class="abs hero-title center">We are an online training website for kids from<br>2 years to 12 years</div>
<svg class="abs" style="left:578px;top:338px" width="44" height="44" viewBox="0 0 44 44"><circle cx="22" cy="22" r="20" fill="none" stroke="#fff" stroke-width="2"/><path d="M17 13 L31 22 L17 31 Z" fill="#fff"/></svg>
<svg class="abs" style="left:173px;top:316px" width="26" height="54" viewBox="0 0 26 54"><path d="M24 2 L2 27 L24 52" fill="none" stroke="#8b8d92" stroke-width="1.5"/></svg>
<svg class="abs" style="left:1002px;top:316px" width="26" height="54" viewBox="0 0 26 54"><path d="M2 2 L24 27 L2 52" fill="none" stroke="#8b8d92" stroke-width="1.5"/></svg>
<div class="hero-btn hero-more">Read More</div>
<div class="hero-btn hero-contact">Contact Now</div>

<!-- who we are -->
<div class="abs who"></div>
<div class="abs section-title center" style="top:664px">WHO WE ARE?</div>
<svg class="abs divider" style="top:699px" viewBox="0 0 60 12"><line x1="0" y1="6" x2="60" y2="6" stroke="#2d5bd3" stroke-width="1"/><path d="M30 2 L34 6 L30 10 L26 6 Z" fill="#f2f2f2" stroke="#2d5bd3"/></svg>
<p class="abs body-copy center" style="left:300px;top:732px;width:600px">
Vivamus suscipit tortor eget felis porttitor volutpat. Vestibulum ac diam sit amet quam vehicula elementum sed sit amet dui.<br>
Pellentesque in ipsum id orci porta dapibus. Proin eget tortor risus. Curabitur aliquet quam id dui posuere blandit.<br>
Donec rutrum congue leo eget malesuada. Vivamus suscipit tortor eget felis porttitor volutpat.<br>
Vivamus suscipit tortor eget felis porttitor volutpat. Cras ultricies ligula sed magna dictum porta.<br>
Lorem ipsum dolor sit amet, consectetur adipiscing elit.</p>

<!-- tutors -->
<div class="abs section-title center" style="top:939px">OUR TUTORS</div>
<svg class="abs divider" style="top:975px" viewBox="0 0 60 12"><line x1="0" y1="6" x2="60" y2="6" stroke="#2d5bd3" stroke-width="1"/><path d="M30 2 L34 6 L30 10 L26 6 Z" fill="#fff" stroke="#2d5bd3"/></svg>
<div class="tutor-photo" style="left:0;background:linear-gradient(180deg,#ececec,#cfcfcf)" role="img" aria-label="Portrait of a smiling young male tutor"></div>
<div class="tutor-photo" style="left:200px;background:linear-gradient(180deg,#e6e4e2,#b9aea4)" role="img" aria-label="Portrait of a smiling young female tutor"></div>
<div class="abs tutor-card">
  <div class="abs tutor-name center">ELAN MORROW</div>
  <p class="abs tutor-bio center">Vivamus suscipit tortor eget felis porttitor volutpat. Vestibulum ac diam sit amet quam vehicula elementum sed sit amet dui. Pellentesque in ipsum id orci.</p>
  <span class="abs" style="left:82px;top:173px;width:8px;height:8px;border-radius:50%;background:#fff"></span>
  <span class="abs" style="left:110px;top:173px;width:8px;height:8px;border-radius:50%;background:#fff"></span>
</div>
<div class="tutor-photo" style="left:600px;background:linear-gradient(180deg,#eeeeee,#5a5450)" role="img" aria-label="Portrait of a smiling male tutor in a suit"></div>
<div class="tutor-photo" style="left:800px;background:linear-gradient(180deg,#e4e4e4,#d8d8d8)" role="img" aria-label="Portrait of a smiling male tutor in a white shirt"></div>
<div class="tutor-photo" style="left:1000px;background:linear-gradient(180deg,#eeeeee,#d9d6d2)" role="img" aria-label="Portrait of a smiling red-haired female tutor"></div>

<!-- services -->
<div class="abs services" role="img" aria-label="Blurred classroom with a tutor and students"></div>
<div class="abs section-title center" style="top:1301px">OUR SERVICES</div>
<svg class="abs divider" style="top:1337px" viewBox="0 0 60 12"><line x1="0" y1="6" x2="60" y2="6" stroke="#2d5bd3" stroke-width="1"/><path d="M30 2 L34 6 L30 10 L26 6 Z" fill="#e8e6e1" stroke="#2d5bd3"/></svg>
<svg class="abs" style="left:186px;top:1507px" width="12" height="22" viewBox="0 0 12 22"><path d="M10 2 L2 11 L10 20" fill="none" stroke="#4a5a7a" stroke-width="1.6"/></svg>
<svg class="abs" style="left:1004px;top:1507px" width="12" height="22" viewBox="0 0 12 22"><path d="M2 2 L10 11 L2 20" fill="none" stroke="#2d5bd3" stroke-width="1.6"/></svg>

<div class="service-card" style="left:235px">
  <svg width="32" height="32" viewBox="0 0 32 32" fill="none" stroke="#222" stroke-width="1.6"><rect x="4" y="5" width="24" height="16" rx="1"/><line x1="16" y1="21" x2="16" y2="26"/><line x1="10" y1="27" x2="22" y2="27"/></svg>
  <span class="rule"></span>
  <h3>LIVE WEBCAM</h3>
  <p>Vivamus suscipit tortor eget felis porttitor volutpat. Vestibulum ac diam sit amet quam vehicula elementum sed sit amet dui. Pellentesque in ipsum id orci.</p>
</div>
<div class="service-card" style="left:484px">
  <svg width="32" height="32" viewBox="0 0 32 32" fill="none" stroke="#222" stroke-width="1.6"><circle cx="16" cy="16" r="12"/><path d="M16 8 V16 L21 19"/></svg>
  <span class="rule"></span>
  <h3>HOURLY COST</h3>
  <p>Vivamus suscipit tortor eget felis porttitor volutpat. Vestibulum ac diam sit amet quam vehicula elementum sed sit amet dui. Pellentesque in ipsum id orci.</p>
</div>
<div class="service-card" style="left:734px">
  <svg width="32" height="32" viewBox="0 0 32 32" fill="none" stroke="#222" stroke-width="1.6"><path d="M6 26 L8 19 L22 5 L27 10 L13 24 Z"/><line x1="19" y1="8" x2="24" y2="13"/></svg>
  <span class="rule"></span>
  <h3>INTERVIEWS &amp; ASSESSMENTS</h3>
  <p>Vivamus suscipit tortor eget felis porttitor volutpat. Vestibulum ac diam sit amet quam vehicula elementum sed sit amet dui. Pellentesque in ipsum id orci.</p>
</div>

<!-- clients -->
<div class="abs section-title center" style="top:1767px">OUR CLIENTS ARE</div>
<svg class="abs divider" style="top:1808px" viewBox="0 0 60 12"><line x1="0" y1="6" x2="60" y2="6" stroke="#2d5bd3" stroke-width="1"/><path d="M30 2 L34 6 L30 10 L26 6 Z" fill="#fff" stroke="#2d5bd3"/></svg>
<p class="abs center" style="left:300px;top:1839px;width:600px;font-size:9.5px;line-height:15.5px;color:#222">“Vivamus suscipit tortor eget felis porttitor volutpat. Vestibulum ac diam sit amet quam vehicula elementum sed sit amet dui.<br>Pellentesque in ipsum id orci porta dapibus. Proin eget tortor risus. Curabitur aliquet quam id dui posuere blandit”</p>
<p class="abs center" style="left:500px;top:1884px;width:200px;font-size:8px;font-style:italic;color:#999">Mr Lorem Ipsum</p>
<div class="client" style="left:265px"><i></i>Halwick Studio</div>
<div class="client" style="left:445px"><i></i>Marlow Design</div>
<div class="client" style="left:612px"><i></i>Orrin Vale</div>
<div class="client" style="left:806px"><i></i>Tamsin Reed</div>

<!-- footer -->
<div class="abs footer"></div>
<div class="footer-box" style="left:233px;width:357px">
  <div class="footer-title">ABOUT US</div>
  <span class="abs" style="left:169px;top:98px;width:19px;height:1.5px;background:var(--blue)"></span>
  <p class="abs center" style="left:48px;top:130px;width:261px;font-size:9px;line-height:15.5px;color:#e4e4e4">Vivamus suscipit tortor eget felis porttitor volutpat. Vestibulum ac diam sit amet quam vehicula elementum sed sit amet dui. Pellentesque in ipsum id orci porta dapibus. Proin eget tortor risus. Curabitur aliquet quam id dui posuere blandit. Donec rutrum congue leo eget malesuada. Vivamus suscipit tortor eget felis porttitor volutpat. Vivamus suscipit tortor eget felis.</p>
</div>
<div class="footer-box" style="left:609px;width:356px">
  <div class="footer-title">CONTACT US</div>
  <div class="field-label" style="top:91px">EMAIL</div>
  <div class="field-line" style="top:116px"></div>
  <div class="field-label" style="top:156px">MESSAGE</div>
  <div class="field-line" style="top:185px"></div>
  <div class="field-line" style="top:225px"></div>
  <div class="abs" style="left:286px;top:258px;font-family:'Montserrat',sans-serif;font-size:9px;letter-spacing:1px;color:var(--blue)">SEND</div>
</div>

<div class="abs bottom-bar"></div>
<div class="abs" style="left:238px;top:2547px;font-size:8px;color:var(--white)">© 2016 - Yoursite All Right Reserved</div>
<span class="social" style="left:884px"></span>
<span class="social" style="left:918px"></span>
<span class="social" style="left:951px"></span>

</body>
</html>
```